KAJU Freightways #ALLKAJU Business Cards & Letterhead

I am looking to business cards designed for our organization. We are currently undergoing a small re-branding that is taking place. Our organization is called KAJU Freightways and we are headquartered in Phoenix, AZ. We primarily provide transportation and logistics services to the Marlow Parcel Bureau who is our largest customer. I would like to see a design that incorporates name, title, contact info, website, and address (this will be different depending on the employee). I would also like to see some color on the business card using our logo colors or a variation. I would like our logo on the back of the business card with the website displayed. The final design should communicate that we are a next generation transportation operate that focuses on being driver-first, customer-centric, innovative, and sustainable.We would also like our #ALLKAJU catch phrase incorporated as well.

Target Market(s)

Transportation & Logistics

Industry/Entity Type

Trucking Company

Contact Information for Business Card

-First and Last Name
-Position Title
-Contact Phone
-Contact Email
-Physical Address

Font styles to use
Serif

Colors

Designer to choose colors to be used in the design.

Requirements
Must have
• -KAJU logo prominently displayed
• -#ALLKAJU catch phrase used
• -Some amount of color, design gradient, etc.
• -Logo on the back with website listed (https://www.kajufreightco.example)

```html
<!DOCTYPE html>
<html lang="en">
<head>
<meta charset="utf-8">
<title>KAJU Freightways Stationery</title>
<link href="https://fonts.googleapis.com/css2?family=Lato:wght@400;700&display=swap" rel="stylesheet">
<style>
  :root {
    --teal: #043b47;
    --green: #77c143;
    --ink: #4a4a4a;
    --paper: #ffffff;
    --backdrop: #e6e7e9;
    --ghost: rgba(4, 59, 71, 0.08);
  }
  * { box-sizing: border-box; margin: 0; padding: 0; }
  html, body { width: 1200px; height: 1200px; overflow: hidden; }
  body { background: var(--backdrop); font-family: "Lato", sans-serif; position: relative; }

  .letterhead {
    position: absolute; left: 50px; top: 214px; width: 600px; height: 772px;
    background: var(--paper); box-shadow: 0 2px 10px rgba(0,0,0,0.12); overflow: hidden;
  }
  .brand-name {
    position: absolute; display: flex; align-items: center; gap: 8px;
    font-weight: 700; color: var(--teal); letter-spacing: 1px;
  }
  .brand-name .dot { border-radius: 50%; background: var(--green); flex: none; }
  .letterhead .brand-name { left: 57px; top: 42px; font-size: 28px; }
  .letterhead .brand-name .dot { width: 14px; height: 14px; }
  .hashtag { position: absolute; right: 50px; top: 40px; font-size: 12px; color: var(--teal); }

  .letter-body {
    position: absolute; left: 57px; top: 141px; width: 485px;
    font-size: 9.6px; line-height: 17.3px; color: var(--ink);
  }
  .letter-body p { margin-bottom: 17px; text-align: justify; }
  .letter-body .date { margin-bottom: 10px; text-align: left; }
  .letter-body .recipient { line-height: 11.5px; margin-bottom: 32px; text-align: left; }
  .watermark {
    position: absolute; left: 178px; top: 332px; font-size: 82px; font-weight: 700;
    color: var(--ghost); letter-spacing: 2px;
  }
  .sign-off { position: absolute; left: 57px; top: 527px; font-size: 9.6px; color: var(--ink); }
  .sign-line { display: block; width: 140px; height: 1px; background: #bbb; margin: 22px 0 10px; }
  .signer { display: block; font-size: 12.5px; color: #333; margin-bottom: 5px; }

  .band { position: absolute; left: 0; bottom: 0; width: 100%; }
  .letter-footer {
    position: absolute; right: 50px; bottom: 22px; text-align: right;
    color: var(--paper); font-size: 11.5px; line-height: 12px;
  }
  .letter-footer .row { display: flex; justify-content: flex-end; align-items: center; gap: 4px; }
  .letter-footer .address { margin-top: 9px; }
  .letter-footer svg { width: 9px; height: 9px; fill: var(--paper); }

  .envelope {
    position: absolute; left: 680px; width: 466px; height: 232px;
    background: var(--paper); box-shadow: 0 2px 8px rgba(0,0,0,0.12); overflow: hidden;
  }
  .envelope-front { top: 532px; }
  .envelope-front .brand-name { left: 30px; top: 38px; font-size: 19px; gap: 6px; }
  .envelope-front .brand-name .dot { width: 10px; height: 10px; }
  .envelope-front .return-address {
    position: absolute; right: 34px; bottom: 14px; text-align: right;
    font-size: 8.6px; line-height: 11px; color: var(--paper);
  }
  .return-address .company { color: var(--green); text-transform: uppercase; }
  .envelope-back { top: 800px; }
  .envelope-back .flap { position: absolute; left: 0; top: 0; width: 100%; height: 56px; }
  .envelope-back .flap-name {
    position: absolute; left: 0; right: 0; top: 8px; text-align: center;
    font-size: 34px; font-weight: 700; color: rgba(255,255,255,0.08); letter-spacing: 2px;
  }
  .envelope-back .site {
    position: absolute; left: 0; right: 0; bottom: 26px; text-align: center;
    font-size: 8.6px; color: var(--teal);
  }
</style>
</head>
<body>

<section class="letterhead">
  <div class="brand-name"><span class="dot"></span>KAJU</div>
  <div class="hashtag">#ALLKAJU</div>
  <div class="watermark" aria-hidden="true">KAJU</div>

  <div class="letter-body">
    <p class="date">Issuing Date: May 5, 2018</p>
    <p class="recipient">Name Of Employee Mr. XYZABC<br>Address of Employee<br>Address Line 2 etc..</p>
    <p>Dear Mr.XYZABC</p>
    <p>Lorem ipsum dolor sit amet, consectetur adipiscing elit, sed do eiusmod tempor incididunt ut labore et dolore magna aliqua. Ut enim ad minim veniam, quis nostrud exercitation ullamco laboris nisi ut aliquip ex ea commodo consequat. Duis aute irure dolor in reprehenderit in voluptate velit esse cillum dolore eu fugiat nulla pariatur, excepteur sint occaecat cupidatat non proident, sunt in culpa qui officia deserunt mollit anim id est laborum.</p>
    <p>Sed ut perspiciatis unde omnis iste natus error sit voluptatem accusantium doloremque laudantium, totam rem aperiam, eaque ipsa quae ab illo inventore veritatis et quasi architecto beatae vitae dicta sunt explicabo nemo enim ipsam.</p>
    <p>Nemo enim ipsam voluptatem quia voluptas sit aspernatur aut odit aut fugit, sed quia consequuntur magni dolores eos qui ratione voluptatem sequi nesciunt, neque porro quisquam est.</p>
  </div>

  <div class="sign-off">
    Yours Sincerely
    <span class="sign-line"></span>
    <span class="signer">Daniel Harrow</span>
    Managing Director
  </div>

  <svg class="band" viewBox="0 0 600 120" preserveAspectRatio="none" aria-hidden="true">
    <path d="M0,62 Q300,78 600,14 L600,120 L0,120 Z" fill="var(--teal)"/>
    <path d="M0,52 Q300,68 600,4" fill="none" stroke="var(--green)" stroke-width="4"/>
  </svg>

  <div class="letter-footer">
    <div class="row">044-555 218 604
      <svg viewBox="0 0 10 10"><path d="M1,3 Q5,0 9,3 L8,4.5 L6.5,3.5 L3.5,3.5 L2,4.5 Z M2.5,5 L7.5,5 L8.5,9 L1.5,9 Z"/></svg></div>
    <div class="row">info@kajufreight.example
      <svg viewBox="0 0 10 10"><path d="M0,2 L10,2 L10,8 L0,8 Z M0.8,2.6 L5,5.6 L9.2,2.6" stroke="var(--teal)" stroke-width="0.8"/></svg></div>
    <div class="row">www.kajufreightco.example
      <svg viewBox="0 0 10 10"><circle cx="5" cy="5" r="4.6"/><path d="M1,5 L9,5 M5,0.6 Q8,5 5,9.4 Q2,5 5,0.6" fill="none" stroke="var(--teal)" stroke-width="0.7"/></svg></div>
    <div class="address">18 Canyon Road, Phoenix AZ, 85004</div>
  </div>
</section>

<section class="envelope envelope-front">
  <div class="brand-name"><span class="dot"></span>KAJU</div>
  <svg class="band" viewBox="0 0 466 70" preserveAspectRatio="none" aria-hidden="true">
    <path d="M0,40 Q233,52 466,8 L466,70 L0,70 Z" fill="var(--teal)"/>
    <path d="M0,32 Q233,44 466,1" fill="none" stroke="var(--green)" stroke-width="3"/>
  </svg>
  <div class="return-address">
    <div class="company">KAJU Freightways</div>
    <div>18 Canyon Road, Phoenix AZ, 85004</div>
  </div>
</section>

<section class="envelope envelope-back">
  <svg class="flap" viewBox="0 0 466 56" preserveAspectRatio="none" aria-hidden="true">
    <path d="M0,0 L466,0 L448,56 L18,56 Z" fill="var(--teal)"/>
  </svg>
  <div class="flap-name" aria-hidden="true">KAJU</div>
  <div class="site">www.kajufreightco.example</div>
</section>

</body>
</html>
```